Sophisticated, clean website reflecting my feminine, playful side to sell my abstract art,

I need a website no more than 3 pages to showcase my paintings, a little about me and some contact info. I do abstracts so looking for something a little edgy, yet feminine and current.
Updates

Hi there, These are some artists websites that I Iike: Marnelvoss.com (I like how airy it is) peterwallombry.com garethpolvens.com (I like how it scrolls) I'll need a place for a photo ( a headshot-i do not have it yet so I'll need to be able to upload that later) as well as an area for my bio. Also, it's important that I will be able to upload any new photos and descriptions easily so it should be user friendly. Lastly, I like in a sunny place so would like to have this seem upbeat and playful as that is how i like to paint. thanks-I'm trying to upload my photos now -

Target Market(s)

ppl ages 35-70 who want large scale art for their homes

Industry/Entity Type

art

Coding

Coded - Design and coding required

Number of Pages Required

3 page

Colors

Designer to choose colors to be used in the design.

Requirements
Must have
• photos of my art, a place for my bio, be easy to reach me. tasteful-nothing too "in your face" -my clients are pretty high end and organized. They like clean lines
Nice to have
• sophisticated background, muted tones in the back-similar clean font throughout-no cursive
Should not have
• too many dark areas. Too many blocks of color. Too serious.

```html
<!DOCTYPE html>
<html lang="en">
<head>
<meta charset="utf-8">
<title>Lena Marlowe — Abstract Art</title>
<link href="https://fonts.googleapis.com/css2?family=Oswald:wght@300;400&family=Quicksand:wght@400;500&display=swap" rel="stylesheet">
<style>
  :root{
    --ink:#3a3a3a;
    --ink-soft:#6b6b6b;
    --line:#bdbdbd;
    --page:#f3f3f3;
    --page-deep:#ebebeb;
    --white:#ffffff;
    --hero-a:#5f9a4a;
    --hero-b:#dfe8d6;
    --hero-c:#2e6f6a;
    --art-a:#d8c79e;
    --art-b:#e4e4de;
    --art-c:#b9c3cf;
  }
  *{margin:0;padding:0;box-sizing:border-box}
  html,body{width:1200px;height:3084px;overflow:hidden}
  body{
    position:relative;
    background:linear-gradient(180deg,var(--white) 0,var(--white) 840px,var(--page) 1000px,var(--page-deep) 3000px);
    font-family:'Quicksand',sans-serif;color:var(--ink);
  }
  .site-header{position:absolute;top:0;left:0;width:1200px;height:180px;background:var(--white)}
  .brand{
    position:absolute;top:14px;left:0;width:1200px;text-align:center;
    font-family:'Quicksand',sans-serif;font-weight:400;font-size:50px;letter-spacing:6px;color:var(--ink);
  }
  .brand-mark{display:inline-block;width:26px;height:26px;background:var(--ink);margin:0 20px;vertical-align:6px}
  .main-nav{position:absolute;top:118px;left:0;width:1200px;height:62px;border-top:1px solid #e6e6e6}
  .main-nav a{
    position:absolute;top:14px;font-family:'Oswald',sans-serif;font-weight:300;font-size:19px;
    color:var(--ink);text-decoration:none;letter-spacing:.5px;
  }
  .main-nav a.active{border-bottom:1px solid var(--ink);padding-bottom:4px}
  .hero{
    position:absolute;top:180px;left:0;width:1200px;height:660px;
    background:linear-gradient(120deg,var(--hero-b) 0%,var(--hero-a) 30%,var(--hero-c) 55%,var(--hero-b) 75%,#8a6a4a 100%);
  }
  .slider-arrow{position:absolute}
  .section-title{
    font-family:'Oswald',sans-serif;font-weight:300;font-size:58px;letter-spacing:2px;color:var(--ink);
  }
  .section-title::after{content:"";display:block;height:1px;background:var(--line);margin-top:4px}
  .about-photo{
    position:absolute;top:1024px;left:108px;width:332px;height:376px;
    border:1px solid var(--line);padding:10px;background:var(--white);
  }
  .about-photo div{width:100%;height:100%;background:linear-gradient(180deg,#e9e6e3,#cfc6bf)}
  .about-title{position:absolute;top:1010px;left:500px}
  .about-title::after{width:200px}
  .about-text{position:absolute;top:1114px;left:500px;width:660px;font-size:19px;line-height:30px;color:var(--ink-soft)}
  .about-text p+p{margin-top:12px}
  .gallery-title{position:absolute;top:1596px;left:0;width:1200px;text-align:center}
  .gallery-title::after,.contact-title::after{width:190px;margin-left:auto;margin-right:auto}
  .gallery-art{
    position:absolute;top:1732px;left:144px;width:912px;height:560px;
    background:linear-gradient(135deg,var(--art-a) 0%,var(--art-b) 50%,var(--art-c) 100%);
  }
  .contact-title{position:absolute;top:2496px;left:0;width:1200px;text-align:center}
  .contact-item{position:absolute;top:2690px;width:240px;text-align:center;font-size:18px;color:var(--ink)}
  .contact-item svg{display:block;margin:0 auto 18px}
  .site-footer{
    position:absolute;top:3000px;left:0;width:1200px;height:84px;border-top:1px solid #dcdcdc;
    text-align:center;font-size:15px;line-height:80px;color:var(--ink);
  }
</style>
</head>
<body>
<header class="site-header">
  <div class="brand">LENA<span class="brand-mark"></span>MARLOWE</div>
  <nav class="main-nav">
    <a class="active" href="#" style="left:248px">HOME</a>
    <a href="#" style="left:428px">ABOUT ME</a>
    <a href="#" style="left:644px">GALLERY</a>
    <a href="#" style="left:850px">CONTACT ME</a>
  </nav>
</header>

<section class="hero" role="img" aria-label="Abstract painting in greens, teal and earthy brown brushstrokes">
  <svg class="slider-arrow" style="left:1140px;top:302px" width="24" height="44" viewBox="0 0 24 44"><path d="M3 3l18 19L3 41" fill="none" stroke="#fff" stroke-width="3"/></svg>
</section>

<section class="about">
  <div class="about-photo"><div role="img" aria-label="Headshot portrait of the artist"></div></div>
  <h2 class="section-title about-title">ABOUT ME</h2>
  <div class="about-text">
    <p>Lorem ipsum dolor sit amet, consectetur adipiscing elit, sed do eiusmod tempor incididunt ut labore et dolore magna aliqua. Ut enim ad minim veniam, quis nostrud exercitation Lorem ipsum dolor sit amet, consectetur adipiscing elit, sed do eiusmod tempor incididunt ut labore et dolore m, quis nostrud exercitati.</p>
    <p>Duis aute irure dolor in reprehenderit in voluptate velit esse cillum dolore eu fugiat nulla pariatur. Excepteur sint occaecat cupidatat non proident, sunt in culpa qui officia deserunt mollit anim id exercitation Lorem ipsum dolor sit amet, consectetur adipiscing.</p>
  </div>
</section>

<section class="gallery">
  <h2 class="section-title gallery-title">GALLERY</h2>
  <svg class="slider-arrow" style="left:62px;top:1990px" width="22" height="40" viewBox="0 0 22 40"><path d="M19 2L3 20l16 18" fill="none" stroke="#9a9a9a" stroke-width="2.5"/></svg>
  <div class="gallery-art" role="img" aria-label="Featured abstract painting from the gallery"></div>
  <svg class="slider-arrow" style="left:1114px;top:1990px" width="22" height="40" viewBox="0 0 22 40"><path d="M3 2l16 18L3 38" fill="none" stroke="#9a9a9a" stroke-width="2.5"/></svg>
</section>

<section class="contact">
  <h2 class="section-title contact-title">CONTACT ME</h2>
  <div class="contact-item" style="left:144px">
    <svg width="40" height="30" viewBox="0 0 40 30"><rect x="2" y="2" width="36" height="26" fill="none" stroke="#3a3a3a" stroke-width="2"/><path d="M2 3l18 14L38 3" fill="none" stroke="#3a3a3a" stroke-width="2"/></svg>
    info@lenamarlowe.com
  </div>
  <div class="contact-item" style="left:420px">
    <svg width="34" height="34" viewBox="0 0 34 34"><path d="M8 2l6 8-3 4c2 4 5 7 9 9l4-3 8 6-3 6C16 31 3 18 2 8z" fill="none" stroke="#3a3a3a" stroke-width="2" stroke-linejoin="round"/></svg>
    Phone: (555) 014 2288
  </div>
  <div class="contact-item" style="left:660px">
    <svg width="34" height="34" viewBox="0 0 34 34"><circle cx="17" cy="17" r="15" fill="none" stroke="#3a3a3a" stroke-width="2"/></svg>
    @lmarloweart
  </div>
  <div class="contact-item" style="left:880px">
    <svg width="34" height="34" viewBox="0 0 34 34"><circle cx="17" cy="17" r="15" fill="none" stroke="#3a3a3a" stroke-width="2"/></svg>
    @lmpainter
  </div>
</section>

<footer class="site-footer">© 2022 Lena Marlowe &nbsp; All Rights Reserved</footer>
</body>
</html>
```